Website redesign for job agency recruitment

Please refer to the attached document, “Tarvenly Work Website Brief,” for comprehensive details regarding the scope, objectives, and requirements of this website redesign project.

For imagery you can use images from this website https://www.pixelmarrowfoto.com or any other you regularly use.

Target Market(s)

Jobseekers and Companies looking for general labour

Industry/Entity Type

Services: Oil, Gas and Mining, Administrative, Construction and Trades, Warehouse and Logistics and, Manufacturing.

Number of Pages Required

5+ page

Font styles to use
Serif
Other font styles liked:
• Inter, Open-Sans or similar.

Requirements
Must have
• The requirements highlighted in the Word document attached. The final design needs to be provided in Figma including all viewports (Desktop, mobiel and tablet)
Should not have
• Website we like as a reference: www.brevicktalentco.com, www.qelvaworks.com, www.zunmarra.com, www.ferrowhires.com, www.9vtalentpool.com, www.hiringwithtrello.ca

```html
<!DOCTYPE html>
<html lang="en">
<head>
<meta charset="utf-8">
<title>Tarvenly Work Agency Ltd. — Staffing Services</title>
<link href="https://fonts.googleapis.com/css2?family=Inter:wght@400;500;600&family=Saira+Condensed:wght@500;600;700&display=swap" rel="stylesheet">
<style>
:root{
  --blue:#0a56d6;
  --blue-dark:#0a3a9c;
  --navy:#1b2a6b;
  --yellow:#f2bd1d;
  --ink:#111111;
  --text:#333333;
  --muted:#6b6b6b;
  --dark:#1b1b1c;
  --white:#ffffff;
}
*{margin:0;padding:0;box-sizing:border-box}
html,body{width:1200px;height:2469px;overflow:hidden;background:var(--white)}
body{position:relative;font-family:"Inter",sans-serif;color:var(--text)}
.abs{position:absolute}
.display{font-family:"Saira Condensed",sans-serif;font-weight:700;text-transform:uppercase;letter-spacing:.5px}
.btn{position:absolute;display:flex;align-items:center;justify-content:center;background:var(--blue);color:var(--white);border-radius:24px;font-size:14px;font-weight:500;box-shadow:0 3px 6px rgba(0,0,0,.2)}

/* header */
.topline{top:0;left:0;width:1200px;height:3px;background:linear-gradient(90deg,transparent,var(--yellow) 20%,var(--yellow) 80%,transparent)}
.brand{left:111px;top:58px;font-size:22px;font-weight:600;color:var(--navy);display:flex;align-items:center;gap:10px}
.brand-dot{width:30px;height:30px;border-radius:50%;background:var(--yellow)}
.brand-tag{left:151px;top:92px;font-size:10px;color:var(--muted)}
.phone-icon{left:672px;top:34px;width:44px;height:44px;border-radius:50%;background:var(--blue);display:flex;align-items:center;justify-content:center;box-shadow:0 2px 5px rgba(0,0,0,.2)}
.toll-label{left:739px;top:37px;font-size:12px;font-weight:500;color:var(--ink)}
.toll-num{left:739px;top:56px;font-size:19px;font-weight:600;color:var(--blue)}
.nav{top:107px;left:393px;display:flex;gap:0;font-size:15px;color:var(--ink)}
.nav span{position:absolute;white-space:nowrap}
.nav .active{color:var(--blue)}

/* hero */
.hero{top:163px;left:0;width:1200px;height:642px;overflow:hidden}
.hero-photo{position:absolute;inset:0;background:linear-gradient(90deg,#1d2a33 0%,#2a3640 35%,#5a4a3a 58%,#d98a3a 68%,#f1b060 80%,#c9a27a 100%)}
.hero-kicker{left:109px;top:129px;font-family:"Saira Condensed",sans-serif;font-size:17px;font-weight:600;color:var(--white)}
.hero-h1{left:109px;top:155px;font-size:39px;line-height:1;color:var(--white)}
.hero-h2{left:109px;top:203px;font-size:58px;line-height:1;color:var(--white)}
.hero-p{left:111px;top:275px;width:500px;font-size:14px;line-height:26px;color:var(--white)}

/* services */
.eyebrow{left:0;width:1200px;top:907px;text-align:center;font-family:"Saira Condensed",sans-serif;font-size:25px;font-weight:500;color:var(--blue)}
.section-title{left:0;width:1200px;top:940px;text-align:center;font-size:45px;color:var(--ink)}
.section-lead{left:0;width:1200px;top:1000px;text-align:center;font-size:15.5px;line-height:28px;color:var(--muted)}
.service{position:absolute;top:1097px;width:160px;text-align:center}
.service .disc{width:86px;height:86px;margin:0 auto;border-radius:50%;background:var(--yellow);display:flex;align-items:center;justify-content:center;box-shadow:3px 4px 6px rgba(0,0,0,.18)}
.service.active .disc{background:var(--blue)}
.service .label{margin-top:16px;font-size:15px;font-weight:500;line-height:21px;color:var(--ink)}
.service.active .label{color:var(--blue)}

/* feature */
.feature-photo{left:112px;top:1313px;width:487px;height:431px;border-radius:42px;background:linear-gradient(135deg,#c9ccd6,#e8ecf2 55%,#bfc6d2)}
.feature-title{left:671px;top:1328px;font-size:35px;color:var(--ink)}
.feature-p{left:673px;width:416px;font-size:14.5px;line-height:28px;color:var(--muted);text-align:justify}
.ticks{left:693px;top:1566px;list-style:none;font-size:14.5px;color:var(--muted)}
.ticks li{display:flex;align-items:center;gap:13px;height:30px}

/* footer */
.footer-bg{left:0;top:1870px;width:1200px;height:599px}
.f-brand{left:111px;top:2232px;font-size:18px;font-weight:500;color:var(--white);display:flex;align-items:center;gap:10px}
.f-brand-dot{width:24px;height:24px;border-radius:50%;background:var(--yellow)}
.f-tag{left:111px;top:2257px;font-size:10px;color:#d0d0d0}
.f-head{top:2103px;font-size:27px;color:var(--white)}
.f-list{list-style:none;font-size:14.5px;color:var(--white)}
.f-list li{height:37.8px;display:flex;align-items:center;gap:22px}
.f-list .ic{width:16px;display:flex;justify-content:center}
.social{top:2106px;width:38px;height:38px;border-radius:50%;background:var(--blue)}
.divider{left:111px;top:2405px;width:978px;border-top:1px dotted #9a9a9a}
.copy{left:111px;top:2430px;font-size:14px;color:var(--white)}
.legal{right:111px;top:2430px;font-size:14px;color:var(--yellow)}
</style>
</head>
<body>

<div class="abs topline"></div>

<header>
  <div class="abs brand"><span class="brand-dot"></span>Tarvenly Work</div>
  <div class="abs brand-tag">The right people to power your business</div>

  <div class="abs phone-icon">
    <svg width="20" height="20" viewBox="0 0 24 24"><path fill="#fff" d="M6.6 10.8a15 15 0 0 0 6.6 6.6l2.2-2.2c.3-.3.7-.4 1-.2 1.1.4 2.3.6 3.6.6.6 0 1 .4 1 1V20c0 .6-.4 1-1 1A17 17 0 0 1 3 4c0-.6.4-1 1-1h3.5c.6 0 1 .4 1 1 0 1.3.2 2.5.6 3.6.1.3 0 .7-.2 1z"/></svg>
  </div>
  <div class="abs toll-label">Toll Free:</div>
  <div class="abs toll-num">1-888-555-0142</div>
  <div class="btn" style="left:920px;top:34px;width:168px;height:44px">For Employers</div>

  <nav class="abs nav">
    <span class="active" style="left:0">HOME</span>
    <span style="left:95px">Candidates</span>
    <span style="left:225px">Companies</span>
    <span style="left:355px">About Us</span>
    <span style="left:469px">Contact Us</span>
    <span style="left:598px">Forms &amp; Links</span>
  </nav>
</header>

<section class="abs hero">
  <div class="hero-photo" role="img" aria-label="Glass office tower beside a city skyline at sunset"></div>
  <div class="abs hero-kicker">Tarvenly Work Agency Ltd</div>
  <div class="abs display hero-h1">The right people to</div>
  <div class="abs display hero-h2">Power your business</div>
  <p class="abs hero-p">Tarvenly Work Agency offers a complete range of staffing services to keep pace with your career or operational demands.</p>
  <div class="btn" style="left:111px;top:346px;width:167px;height:43px">For Candidates</div>
  <div class="btn" style="left:302px;top:346px;width:167px;height:43px">For Employers</div>
  <svg class="abs" style="left:0;top:0" width="1200" height="642" viewBox="0 0 1200 642">
    <path fill="#fff" d="M0 642 L0 520 C120 600 300 640 520 630 C760 620 940 480 1200 530 L1200 642 Z"/>
    <path fill="var(--blue)" d="M0 512 C110 600 250 630 420 620 C620 608 800 500 960 480 C1060 468 1140 480 1200 492 L1200 520 C1080 500 960 505 800 560 C640 612 480 640 340 642 L0 642 Z"/>
    <path fill="var(--blue-dark)" d="M340 640 C520 630 700 580 860 540 C980 510 1100 505 1200 520 L1200 532 C1080 520 960 530 820 575 C680 620 520 642 380 642 Z"/>
    <path fill="#fff" d="M0 642 L0 600 C120 630 260 642 360 642 Z"/>
  </svg>
</section>

<main>
  <div class="abs eyebrow">What We Do</div>
  <h2 class="abs display section-title">Services We Provide</h2>
  <p class="abs section-lead">Sed ut perspiciatis unde omnis iste natus error sit voluptatem accusantium dolore<br>mque laudantium, totam rem aperiam, eaque ipsa quae ab illo inven</p>

  <div class="service" style="left:105px">
    <div class="disc"><svg width="40" height="40" viewBox="0 0 40 40"><rect x="6" y="8" width="16" height="24" rx="2" fill="var(--blue-dark)"/><path d="M29 14 C33 21 35 24 35 27 a6 6 0 0 1-12 0 c0-3 2-6 6-13z" fill="var(--blue)"/></svg></div>
    <div class="label">OIL</div>
  </div>
  <div class="service" style="left:250px">
    <div class="disc"><svg width="40" height="40" viewBox="0 0 40 40"><path d="M8 14 C16 6 28 6 34 14 C27 10 18 10 8 14z" fill="var(--blue-dark)"/><rect x="19" y="10" width="4" height="24" transform="rotate(25 21 22)" fill="var(--blue-dark)"/><path d="M6 34 L16 22 L22 34z" fill="var(--blue)"/></svg></div>
    <div class="label">GAS &amp; MINING</div>
  </div>
  <div class="service" style="left:417px">
    <div class="disc"><svg width="44" height="44" viewBox="0 0 44 44"><circle cx="22" cy="22" r="13" fill="none" stroke="var(--blue-dark)" stroke-width="8" stroke-dasharray="6 4"/><circle cx="22" cy="22" r="12" fill="none" stroke="var(--blue-dark)" stroke-width="4"/><circle cx="22" cy="22" r="5" fill="var(--yellow)"/></svg></div>
    <div class="label">ADMINISTRATIVE</div>
  </div>
  <div class="service active" style="left:583px">
    <div class="disc"><svg width="44" height="44" viewBox="0 0 44 44"><path d="M9 22 a13 13 0 0 1 26 0z" fill="#fff"/><rect x="6" y="22" width="32" height="4" rx="2" fill="#fff"/><circle cx="22" cy="32" r="6" fill="none" stroke="#fff" stroke-width="3"/></svg></div>
    <div class="label">CONSTRUCTION<br>&amp; TRADES</div>
  </div>
  <div class="service" style="left:748px">
    <div class="disc"><svg width="44" height="44" viewBox="0 0 44 44"><path d="M6 16 L22 6 L38 16 L38 36 L6 36z" fill="var(--blue-dark)"/><rect x="12" y="20" width="20" height="16" fill="var(--yellow)"/><rect x="14" y="24" width="7" height="7" fill="var(--blue)"/><rect x="23" y="24" width="7" height="7" fill="var(--blue)"/></svg></div>
    <div class="label">WAREHOUSE &amp;<br>LOGISTICS</div>
  </div>
  <div class="service" style="left:912px">
    <div class="disc"><svg width="44" height="44" viewBox="0 0 44 44"><circle cx="22" cy="12" r="6" fill="none" stroke="var(--blue-dark)" stroke-width="4"/><rect x="10" y="21" width="10" height="8" fill="var(--blue-dark)"/><rect x="24" y="21" width="10" height="8" fill="var(--blue-dark)"/><rect x="5" y="30" width="34" height="6" rx="3" fill="var(--blue-dark)"/></svg></div>
    <div class="label">MANUFACTURING</div>
  </div>

  <div class="abs feature-photo" role="img" aria-label="Team reviewing construction blueprints with a hard hat, calculator and drafting tools"></div>
  <h3 class="abs display feature-title">Construction &amp; Trades</h3>
  <p class="abs feature-p" style="top:1377px">Sed ut perspiciatis unde omnis iste natus error sit voluptatem accusantium doloremque laudantium.</p>
  <p class="abs feature-p" style="top:1462px">Nemo enim ipsam voluptatem quia voluptas sit aspernatur aut odit aut fugit, sed quia consequuntur magni dolores eos qui ratione voluptatem sequi nesciunt.</p>
  <ul class="abs ticks">
    <li><svg width="15" height="15" viewBox="0 0 16 16"><circle cx="8" cy="8" r="7.5" fill="var(--blue)"/><path d="M4.5 8.2 L7 10.5 L11.5 5.5" fill="none" stroke="#fff" stroke-width="1.8"/></svg>Ut enim ad minima veniam</li>
    <li><svg width="15" height="15" viewBox="0 0 16 16"><circle cx="8" cy="8" r="7.5" fill="var(--blue)"/><path d="M4.5 8.2 L7 10.5 L11.5 5.5" fill="none" stroke="#fff" stroke-width="1.8"/></svg>Quis nostrum exercitationem ullam corporis</li>
    <li><svg width="15" height="15" viewBox="0 0 16 16"><circle cx="8" cy="8" r="7.5" fill="var(--blue)"/><path d="M4.5 8.2 L7 10.5 L11.5 5.5" fill="none" stroke="#fff" stroke-width="1.8"/></svg>Aliquid ex ea commodi consequatur</li>
  </ul>
  <div class="btn" style="left:673px;top:1679px;width:148px;height:43px">View Details</div>
</main>

<footer>
  <svg class="abs footer-bg" width="1200" height="599" viewBox="0 0 1200 599">
    <rect x="0" y="150" width="1200" height="449" fill="var(--dark)"/>
    <path fill="var(--dark)" d="M0 150 C300 150 560 70 800 50 C980 40 1100 80 1200 140 L1200 160 L0 160z"/>
    <path fill="var(--blue)" d="M0 145 C250 175 520 110 760 75 C960 45 1100 60 1200 130 L1200 140 C1100 80 980 40 800 52 C560 70 300 152 0 150z"/>
    <path fill="var(--blue)" d="M0 150 C200 160 420 130 600 95 C780 62 950 20 1200 115 L1200 130 C1080 55 950 38 780 62 C560 95 300 170 0 150z"/>
    <path fill="#fff" d="M0 136 C250 150 520 70 740 30 C800 20 840 14 860 12 C780 24 560 80 380 120 C240 150 100 150 0 145z"/>
    <path fill="var(--yellow)" d="M0 120 C200 140 420 90 620 45 C720 22 800 14 850 12 C780 16 640 50 500 90 C340 135 160 148 0 136z"/>
  </svg>

  <div class="abs f-brand"><span class="f-brand-dot"></span>Tarvenly Work Agency Ltd.</div>
  <div class="abs f-tag">The right people to power your business</div>

  <h4 class="abs display f-head" style="left:390px">Quick Links</h4>
  <ul class="abs f-list" style="left:390px;top:2148px">
    <li><span class="ic"><svg width="14" height="14" viewBox="0 0 16 16"><circle cx="8" cy="8" r="7.5" fill="#fff"/><path d="M4 8 H11 M8 5 L11 8 L8 11" fill="none" stroke="var(--dark)" stroke-width="1.8"/></svg></span>Home</li>
    <li><span class="ic"><svg width="14" height="14" viewBox="0 0 16 16"><circle cx="8" cy="8" r="7.5" fill="#fff"/><path d="M4 8 H11 M8 5 L11 8 L8 11" fill="none" stroke="var(--dark)" stroke-width="1.8"/></svg></span>Candidate</li>
    <li><span class="ic"><svg width="14" height="14" viewBox="0 0 16 16"><circle cx="8" cy="8" r="7.5" fill="#fff"/><path d="M4 8 H11 M8 5 L11 8 L8 11" fill="none" stroke="var(--dark)" stroke-width="1.8"/></svg></span>Companies</li>
    <li><span class="ic"><svg width="14" height="14" viewBox="0 0 16 16"><circle cx="8" cy="8" r="7.5" fill="#fff"/><path d="M4 8 H11 M8 5 L11 8 L8 11" fill="none" stroke="var(--dark)" stroke-width="1.8"/></svg></span>About Us</li>
    <li><span class="ic"><svg width="14" height="14" viewBox="0 0 16 16"><circle cx="8" cy="8" r="7.5" fill="#fff"/><path d="M4 8 H11 M8 5 L11 8 L8 11" fill="none" stroke="var(--dark)" stroke-width="1.8"/></svg></span>Contact Us</li>
    <li><span class="ic"><svg width="14" height="14" viewBox="0 0 16 16"><circle cx="8" cy="8" r="7.5" fill="#fff"/><path d="M4 8 H11 M8 5 L11 8 L8 11" fill="none" stroke="var(--dark)" stroke-width="1.8"/></svg></span>Forms &amp; Links</li>
  </ul>

  <h4 class="abs display f-head" style="left:608px">Let’s Connect</h4>
  <ul class="abs f-list" style="left:608px;top:2148px">
    <li><span class="ic"><svg width="14" height="14" viewBox="0 0 16 16"><rect x="0.5" y="0.5" width="15" height="15" rx="3" fill="#fff"/><path fill="var(--dark)" d="M5 4 L7 4 L7.5 6.5 L6.4 7.3 a6 6 0 0 0 2.3 2.3 L9.5 8.5 L12 9 L12 11 C8 11.5 4.5 8 5 4z"/></svg></span>778-555-0198 (British Columbia)</li>
    <li><span class="ic"></span>403-555-0176 (Alberta)</li>
    <li><span class="ic"><svg width="15" height="12" viewBox="0 0 16 12"><rect width="16" height="12" rx="1.5" fill="#fff"/><path d="M1 1.5 L8 7 L15 1.5" fill="none" stroke="var(--dark)" stroke-width="1.5"/></svg></span>info@tarvenlywork.com</li>
    <li><span class="ic"><svg width="14" height="14" viewBox="0 0 16 16" fill="#fff"><rect x="6" y="1" width="4" height="4"/><rect x="1" y="11" width="4" height="4"/><rect x="6" y="11" width="4" height="4"/><rect x="11" y="11" width="4" height="4"/><path d="M7.3 5 h1.4 v3 h5 v3 h-1.4 v-1.6 h-3.6 v1.6 h-1.4 v-1.6 h-3.6 v1.6 h-1.4 v-3 h5z"/></svg></span>2210 Marlow Quay Street, Suite 400</li>
    <li><span class="ic"></span>Vancouver, BC V6E 0Z1</li>
    <li><span class="ic"></span>Canada</li>
  </ul>

  <span class="abs social" style="left:915px" aria-label="Social link 1"></span>
  <span class="abs social" style="left:960px" aria-label="Social link 2"></span>
  <span class="abs social" style="left:1006px" aria-label="Social link 3"></span>
  <span class="abs social" style="left:1051px" aria-label="Social link 4"></span>

  <div class="abs divider"></div>
  <div class="abs copy">© Tarvenly Work Agency Ltd. | All rights reserved 2026</div>
  <div class="abs legal">Terms of Use &nbsp;&nbsp;|&nbsp;&nbsp; Login</div>
</footer>

</body>
</html>
```